Income Tax Business Cards - Updates

Need to update these business cards while keeping all the same wording but just update them and make them look nicer and more modern/ on brand with our brand.

Industry/Entity Type

finance

Contact Information for Business Card

we have multiple locations so will just need to easily be able to change the address and phone numbers

Colors

Designer to choose colors to be used in the design.

```html
<!DOCTYPE html>
<html lang="en">
<head>
<meta charset="utf-8">
<title>Ledgerline Financial – Business Card</title>
<link rel="stylesheet" href="https://fonts.googleapis.com/css2?family=Lato:wght@400;700;900&display=swap">
<style>
  :root {
    --stage: #8f8f8f;
    --brand-green: #0e522f;
    --brand-red: #c41f28;
    --paper: #ffffff;
    --ink: #2b2b2b;
  }
  * { box-sizing: border-box; margin: 0; padding: 0; }
  html, body { width: 1200px; height: 1200px; overflow: hidden; }
  body {
    background: var(--stage);
    font-family: "Lato", sans-serif;
    position: relative;
  }
  .card {
    position: absolute;
    left: 250px;
    width: 700px;
    height: 400px;
    border-radius: 22px;
    overflow: hidden;
    box-shadow: 0 3px 8px rgba(0,0,0,0.25);
  }
  .card-front { top: 170px; background: var(--paper); }
  .card-back { top: 631px; background: var(--brand-green); }

  .wordmark {
    position: absolute;
    display: flex;
    align-items: center;
    gap: 10px;
    font-weight: 900;
    letter-spacing: 0.3px;
    white-space: nowrap;
  }
  .wordmark-dot { border-radius: 50%; flex: none; }
  .card-front .wordmark {
    left: 20px; width: 320px; top: 150px;
    justify-content: center;
    color: var(--brand-green);
    font-size: 29px;
    line-height: 36px;
  }
  .card-front .wordmark-dot { width: 13px; height: 13px; background: var(--brand-red); }

  .divider {
    position: absolute;
    left: 360px; top: 73px;
    width: 1px; height: 190px;
    background: var(--brand-green);
  }
  .contact { position: absolute; left: 394px; top: 66px; color: var(--ink); }
  .contact-name {
    color: var(--brand-green);
    font-weight: 900;
    font-size: 31px;
    line-height: 36px;
    letter-spacing: 0.3px;
  }
  .contact-title {
    color: var(--brand-red);
    font-size: 19px;
    line-height: 24px;
    margin-bottom: 10px;
  }
  .contact-row {
    display: flex;
    align-items: flex-start;
    gap: 11px;
    font-size: 16.5px;
    line-height: 24px;
    letter-spacing: 0.3px;
  }
  .contact-row.phone { font-weight: 700; margin-top: 9px; }
  .contact-row svg { width: 14px; height: 14px; margin-top: 5px; flex: none; fill: var(--brand-red); }

  .offer-band {
    position: absolute;
    top: 316px; height: 84px;
    color: var(--paper);
    font-weight: 900;
    text-transform: uppercase;
    display: flex; flex-direction: column; justify-content: center;
  }
  .offer-advance { left: 0; width: 312px; background: var(--brand-green); padding-left: 33px; }
  .offer-estimate { left: 321px; width: 379px; background: var(--brand-red); align-items: center; }
  .offer-advance .big { font-size: 37px; line-height: 38px; }
  .offer-advance .small { font-size: 22.5px; line-height: 26px; }
  .offer-estimate .small { font-size: 21px; line-height: 24px; }
  .offer-estimate .big { font-size: 39px; line-height: 40px; }

  .card-back .wordmark {
    left: 0; right: 0; top: 135px;
    justify-content: center;
    color: var(--paper);
    font-size: 58px;
    line-height: 70px;
  }
  .card-back .wordmark-dot { width: 20px; height: 20px; background: var(--paper); }
  .back-tagline {
    position: absolute; left: 0; right: 0; top: 307px;
    text-align: center;
    color: var(--paper);
    font-weight: 900;
    text-transform: uppercase;
  }
  .back-tagline .headline { font-size: 33px; line-height: 38px; }
  .back-tagline .subline { font-size: 25px; line-height: 30px; }
</style>
</head>
<body>
  <section class="card card-front">
    <div class="wordmark"><span class="wordmark-dot"></span>Ledgerline Financial</div>
    <div class="divider"></div>
    <div class="contact">
      <div class="contact-name">DANIEL CARTER</div>
      <div class="contact-title">Founder &amp; CEO</div>
      <div class="contact-row address">
        <svg viewBox="0 0 24 24"><path d="M12 1a8 8 0 0 0-8 8c0 6 8 14 8 14s8-8 8-14a8 8 0 0 0-8-8zm0 11a3 3 0 1 1 0-6 3 3 0 0 1 0 6z"/></svg>
        <span>Your Address, City<br>State, Country, Zip 1235</span>
      </div>
      <div class="contact-row phone">
        <svg viewBox="0 0 24 24"><path d="M6.6 10.8a15 15 0 0 0 6.6 6.6l2.2-2.2a1 1 0 0 1 1-.25 11 11 0 0 0 3.6.57 1 1 0 0 1 1 1V20a1 1 0 0 1-1 1A17 17 0 0 1 3 4a1 1 0 0 1 1-1h3.5a1 1 0 0 1 1 1c0 1.25.2 2.45.57 3.6a1 1 0 0 1-.25 1z"/></svg>
        <span>(123) 456-7890</span>
      </div>
      <div class="contact-row">
        <svg viewBox="0 0 24 24"><path d="M2 5h20v14H2zm2 2v.5l8 5 8-5V7zm0 2.8V17h16V9.8l-8 5z"/></svg>
        <span>office@ledgerline.com</span>
      </div>
      <div class="contact-row">
        <svg viewBox="0 0 24 24"><path d="M12 2a10 10 0 1 0 0 20 10 10 0 0 0 0-20zm0 2c1 0 2.3 2 2.8 5H9.2C9.7 6 11 4 12 4zM4.3 11h3c0 .7-.1 1.3 0 2h-3a8 8 0 0 1 0-2zm4.9 0h5.6a15 15 0 0 1 0 2H9.2a15 15 0 0 1 0-2zm7.5 0h3a8 8 0 0 1 0 2h-3c.1-.7 0-1.3 0-2zM12 20c-1 0-2.3-2-2.8-5h5.6c-.5 3-1.8 5-2.8 5z"/></svg>
        <span>www.ledgerline.com</span>
      </div>
    </div>
    <div class="offer-band offer-advance">
      <span class="big">Up to $6,000</span>
      <span class="small">Same day advance</span>
    </div>
    <div class="offer-band offer-estimate">
      <span class="small">On approved tax returns!</span>
      <span class="big">Free estimates!</span>
    </div>
  </section>

  <section class="card card-back">
    <div class="wordmark"><span class="wordmark-dot"></span>Ledgerline Financial</div>
    <div class="back-tagline">
      <div class="headline">File your taxes here</div>
      <div class="subline">Up to $6,000 same day advance</div>
    </div>
  </section>
</body>
</html>
```